Health and Wellness company needs flyer to promote free seminar

Corvella Motion studio is a health and wellness company that offers an exercise program designed by physical therapists to help relieve pain and improve mobility. Our business is a new concept that is not well understood by the public. In order to promote our business we offer a free seminar where we present information regarding the underlying cause of pain and tightness. During the seminar we also perform a posture screen and movement testing for all participants.

Target Market(s)

Mostly healthy and active women ages 25-65

Industry/Entity Type

Health And Wellness

Font styles to use
Sans Serif

Colors

Designer to choose colors to be used in the design.

Requirements
Must have
• Title: Eliminate Pain and Tightness For Good
• Paragraph: Corvella Motion Studio offers a free 60 minute seminar: "The Busy Walker's Manual for Stretching and Living Lighter."
• What to Expect:
• • Identify the underlying cause of your pain and mobility issues
• • Expose what gets in the way of you moving and feeling better
• • Learn why traditional exercises don’t help and can actually make the problem worse
• • Reveal what your posture is saying and how that impacts you
• • Experience your muscle imbalances through movement tests
• • Discover the training method that realigns your posture, increases your mobility and reduces your pain
• Call to action: RSVP online at corvellamotionstudio.com
Nice to have
• Use a relevant image showing a female dealing with tightness in the low back, legs, etc.
• Emphasize that the seminar is FREE.
• Make the call to action prominent.

```html
<!DOCTYPE html>
<html lang="en">
<head>
<meta charset="utf-8">
<title>Corvella Motion Studio – Free Seminar Flyer</title>
<link href="https://fonts.googleapis.com/css2?family=Roboto+Condensed:wght@700&family=Open+Sans:wght@600;700&family=Arimo:wght@700&display=swap" rel="stylesheet">
<style>
  :root {
    --purple: #5a5aa8;
    --orange: #f5921e;
    --ink: #222226;
    --band-grey: #d4d5d8;
    --band-grey-light: #eeeeef;
    --backdrop: #e6e6ea;
    --white: #ffffff;
  }
  * { margin: 0; padding: 0; box-sizing: border-box; }
  html, body { width: 1020px; height: 1200px; overflow: hidden; }
  body { background: var(--backdrop); }

  .flyer {
    position: absolute; left: 85px; top: 0;
    width: 850px; height: 1200px;
    background: var(--white);
    overflow: hidden;
    font-family: "Open Sans", sans-serif;
  }

  .header { position: absolute; left: 0; top: 0; width: 850px; height: 104px; }
  .brand {
    position: absolute; left: 18px; top: 34px; z-index: 2;
    display: flex; align-items: center; gap: 10px;
    color: var(--purple); font-family: "Open Sans", sans-serif;
    font-weight: 700; font-size: 20px; line-height: 36px; white-space: nowrap;
  }
  .brand-square { width: 36px; height: 36px; background: var(--orange); flex: none; }
  .header-tagline {
    position: absolute; left: 321px; top: 0; width: 529px; height: 104px;
    background: var(--purple);
    clip-path: polygon(0 0, 100% 0, 100% 100%, 7% 100%);
    display: flex; align-items: center; justify-content: flex-end; padding-right: 20px;
    color: var(--white); font-family: "Roboto Condensed", sans-serif;
    font-weight: 700; font-size: 24px; letter-spacing: 0.2px; white-space: nowrap;
  }

  .hero-photo {
    position: absolute; left: 0; top: 104px; width: 850px; height: 435px;
    background: linear-gradient(100deg, #f3f3f3 0%, #e4e4e6 35%, #efe6c6 62%, #e8e8ea 100%);
  }

  .seminar-band {
    position: absolute; left: 0; top: 539px; width: 850px; height: 142px;
    background: linear-gradient(180deg, var(--band-grey-light), var(--band-grey));
    text-align: center;
  }
  .seminar-title {
    font-family: "Roboto Condensed", sans-serif; font-weight: 700;
    color: var(--purple); font-size: 41px; line-height: 45px; padding-top: 10px;
  }
  .seminar-subtitle {
    font-family: "Open Sans", sans-serif; font-weight: 700;
    color: var(--ink); font-size: 18px; margin-top: 5px; text-transform: uppercase;
  }

  .expect-bar { position: absolute; left: 0; top: 692px; width: 500px; height: 64px; }
  .expect-label {
    position: absolute; left: 0; top: 0; width: 404px; height: 64px;
    background: var(--purple);
    clip-path: polygon(0 0, 100% 0, 90% 100%, 0 100%);
    color: var(--white); font-family: "Roboto Condensed", sans-serif;
    font-weight: 700; font-size: 43px; line-height: 64px; padding-left: 52px;
  }
  .expect-stripes { position: absolute; left: 392px; top: 0; }

  .expect-list {
    position: absolute; left: 30px; top: 768px; width: 790px;
    list-style: none;
    font-family: "Open Sans", sans-serif; font-weight: 700;
    font-size: 17.5px; line-height: 23px; color: var(--ink);
  }
  .expect-list li { position: relative; padding-left: 20px; margin-bottom: 24px; }
  .expect-list li::before {
    content: ""; position: absolute; left: 0; top: 8px;
    width: 7px; height: 7px; border-radius: 50%; background: var(--orange);
  }

  .signup {
    position: absolute; left: 0; top: 1030px; width: 850px; text-align: center;
    font-family: "Arimo", sans-serif; font-weight: 700; font-size: 35px; color: var(--purple);
  }
  .signup .free { color: var(--orange); }

  .rsvp {
    position: absolute; left: 187px; top: 1083px; width: 477px; height: 46px;
    background: var(--orange);
    clip-path: polygon(4% 0, 100% 0, 96% 100%, 0 100%);
    color: var(--white); font-family: "Open Sans", sans-serif; font-weight: 700;
    font-size: 20px; line-height: 46px; text-align: center; white-space: nowrap;
  }

  .studio {
    position: absolute; top: 1143px; height: 57px;
    color: var(--white); text-align: center;
  }
  .studio-houston { left: 0; width: 460px; background: var(--purple);
    clip-path: polygon(0 0, 100% 0, 96% 100%, 0 100%); padding-right: 20px; }
  .studio-portland { left: 446px; width: 404px; background: var(--orange);
    clip-path: polygon(4% 0, 100% 0, 100% 100%, 0 100%); padding-left: 20px; }
  .studio-name { font-family: "Open Sans", sans-serif; font-weight: 700; font-size: 16px; line-height: 20px; padding-top: 4px; }
  .studio-phone { font-family: "Roboto Condensed", sans-serif; font-weight: 700; font-size: 24px; line-height: 28px; }
</style>
</head>
<body>
  <main class="flyer">
    <header class="header">
      <div class="header-tagline">ELIMINATE PAIN AND TIGHTNESS FOR GOOD</div>
      <div class="brand"><span class="brand-square"></span><span>Corvella Motion studio</span></div>
    </header>

    <div class="hero-photo" role="img" aria-label="Photo of a woman at a desk with a laptop, holding her lower back in pain"></div>

    <section class="seminar-band">
      <h1 class="seminar-title">CORVELLA MOTION STUDIO<br>OFFERS A FREE 60 MINUTE SEMINAR</h1>
      <p class="seminar-subtitle">The Busy Walker's Manual for Stretching and Living Lighter</p>
    </section>

    <div class="expect-bar">
      <div class="expect-label">What to Expect</div>
      <svg class="expect-stripes" width="100" height="64" viewBox="0 0 100 64">
        <polygon points="18,0 34,0 16,64 0,64" fill="#f5921e"/>
        <polygon points="40,0 56,0 38,64 22,64" fill="#f5921e"/>
        <polygon points="62,0 78,0 60,64 44,64" fill="#f5921e"/>
        <polygon points="84,0 100,0 82,64 66,64" fill="#f5921e"/>
      </svg>
    </div>

    <ul class="expect-list">
      <li>Identify the underlying cause of your pain and mobility issues</li>
      <li>Expose what gets in the way of you moving and feeling better</li>
      <li>Learn why traditional exercises don’t help and can actually make the problem worse<br>Reveal what your posture is saying and how that impacts you</li>
      <li>Experience your muscle imbalances through movement tests</li>
      <li>Discover the training method that realigns your posture, increases your mobility and reduces your pain</li>
    </ul>

    <p class="signup">Sign up for the <span class="free">FREE</span> seminar today</p>
    <div class="rsvp">RSVP online at corvellamotionstudio.com</div>

    <footer>
      <div class="studio studio-houston">
        <div class="studio-name">Studio Houston</div>
        <div class="studio-phone">CALL NOW:(281) 555-0147</div>
      </div>
      <div class="studio studio-portland">
        <div class="studio-name">Studio Portland</div>
        <div class="studio-phone">CALL NOW:(503) 555-0182</div>
      </div>
    </footer>
  </main>
</body>
</html>
```